Harborview Estates Business Card for Apartment Buildings

Create business cards for resident managers who run apartment buildings. The audience is the public who are searching for apartment rentals, and current residents who live at the apartment building. Key design element will be incorporating the company logo, however, the logo cannot dominate. The building name and manager name are more important than the logo. Current business card design leaves little room for copy, so we may need to reduce the size on the current card to allow for more space for copy.

Target Market(s)

Adults 18-65 years of age, who are looking for an apartment rental, plus current residents who live at our apartment buildings.

Industry/Entity Type

Property Management

Contact Information for Business Card

A major design element will be use of the company logo. Important property and manager contact information must be part of the design. The size of the logo will need to be reduced to make room for building and manager contact copy.

Font styles to use
Sans Serif

Colors
3176b5
000000
959595
ffffff

Requirements
Must have
• 1) Incorporate the company logo.
• 2) Use the company colors (dark blue, black/grey, over white).
• 3) FEATURE THE BUILDING NAME
• 4) FEATURE THE MANAGER NAME
• 5) The company name is less important than BUILDING and MANAGER
• 6) Manager contact information
• **SEE ATTACHED CREATIVE BRIEF**
Nice to have
• 1) Back of card logo watermark
• 2) Ability to write notes on back of carfd
Should not have
• Avoid letting the company logo dominate the card, the building name and manager are more important than the company logo.

```html
<!DOCTYPE html>
<html lang="en">
<head>
<meta charset="utf-8">
<title>Harborview Estates – Business Card</title>
<link href="https://fonts.googleapis.com/css2?family=Lato:wght@400;700&display=swap" rel="stylesheet">
<style>
  :root {
    --brand-blue: #0f6aa8;
    --ink: #2b2b2b;
    --rule-grey: #959595;
    --paper: #ffffff;
    --backdrop: #343434;
  }
  * { margin: 0; padding: 0; box-sizing: border-box; }
  html, body {
    width: 1200px; height: 900px; overflow: hidden;
    background: var(--backdrop);
    font-family: "Lato", Arial, sans-serif;
  }
  .stage { position: relative; width: 1200px; height: 900px; }
  .card {
    position: absolute; top: 306px; width: 438px; height: 271px;
    background: var(--paper);
    box-shadow: 2px 3px 6px rgba(0,0,0,.45);
    overflow: hidden;
  }
  .card--front { left: 150px; }
  .card--back { left: 609px; width: 440px; }

  /* front */
  .front-band {
    position: absolute; left: 0; top: 0; width: 155px; height: 100%;
    background: var(--brand-blue);
  }
  .front-mark {
    position: absolute; left: 18px; top: 96px; width: 130px;
    display: flex; flex-direction: column; align-items: flex-start; gap: 10px;
  }
  .front-mark__square { width: 22px; height: 22px; background: var(--paper); }
  .front-mark__name {
    font-weight: 700; font-size: 19px; line-height: 1.15; letter-spacing: .3px;
    color: var(--paper); text-transform: uppercase; white-space: nowrap;
  }
  .contact {
    position: absolute; right: 17px; top: 48px; text-align: right;
    color: var(--ink);
  }
  .contact__name {
    font-size: 20px; font-weight: 400; color: var(--brand-blue);
    letter-spacing: .3px; line-height: 22px;
  }
  .contact__title { font-size: 12px; line-height: 14px; }
  .contact__address { margin-top: 38px; font-size: 12.5px; line-height: 15.5px; }
  .contact__lines { margin-top: 9px; list-style: none; font-size: 12px; line-height: 16px; }
  .contact__lines li { display: flex; justify-content: flex-end; align-items: center; gap: 2px; }
  .contact__icon { width: 9px; height: 9px; fill: var(--brand-blue); }

  /* back */
  .back-brand {
    position: absolute; left: 0; right: 0; top: 62px;
    display: flex; justify-content: center; align-items: center; gap: 10px;
  }
  .back-brand__square { width: 22px; height: 22px; background: var(--brand-blue); }
  .back-brand__name {
    font-weight: 700; font-size: 30px; letter-spacing: .5px;
    color: var(--brand-blue); text-transform: uppercase;
  }
  .note-line {
    position: absolute; left: 31px; width: 377px; height: 0;
    border-top: 1.5px solid var(--rule-grey);
  }
</style>
</head>
<body>
<main class="stage">
  <section class="card card--front">
    <div class="front-band"></div>
    <div class="front-mark">
      <div class="front-mark__square"></div>
      <div class="front-mark__name">Harborview<br>Estates</div>
    </div>
    <div class="contact">
      <h1 class="contact__name">DANIEL BROOKS</h1>
      <p class="contact__title">Property Manager</p>
      <p class="contact__address">1820 Harbor Point<br>Road #B210<br>Seattle, WA 98121</p>
      <ul class="contact__lines">
        <li>555-214-7730
          <svg class="contact__icon" viewBox="0 0 10 10"><path d="M1 3.5C1 2 3 1 5 1s4 1 4 2.5H7V2.8H3v.7zM2 5h6l1 4H1z"/></svg></li>
        <li>555-214-7731
          <svg class="contact__icon" viewBox="0 0 10 10"><path d="M3 1h4v2H3zM1 3.5h8v4H7.5V6h-5v1.5H1zM3 6.8h4V9H3z"/></svg></li>
        <li>daniel@harborviewestates.us
          <svg class="contact__icon" viewBox="0 0 10 10"><path d="M1 2.5h8v5H1zM1.5 3 5 5.6 8.5 3" stroke="#fff" stroke-width=".7"/></svg></li>
        <li>www.harborviewestates.us
          <svg class="contact__icon" viewBox="0 0 10 10"><circle cx="5" cy="5" r="4.2"/><path d="M1 5h8M5 .8c-2 2.5-2 5.9 0 8.4M5 .8c2 2.5 2 5.9 0 8.4" stroke="#fff" stroke-width=".6" fill="none"/></svg></li>
      </ul>
    </div>
  </section>

  <section class="card card--back">
    <div class="back-brand">
      <div class="back-brand__square"></div>
      <div class="back-brand__name">Harborview Estates</div>
    </div>
    <div class="note-line" style="top:155px"></div>
    <div class="note-line" style="top:196px"></div>
    <div class="note-line" style="top:235px"></div>
  </section>
</main>
</body>
</html>
```